KBT Business Cards

We require business cards for our business. We would like a matte black back to the card, with our logo centred in the middle. The front side of the card is open to design.

Target Market(s)

Clients looking for legal services (professional)

Industry/Entity Type

Legal

Contact Information for Business Card

Doran Kelbrath
Partner
Mobile: 0461 738 524
Email: doran@kbtlaw.co
Website: www.kbtlaw.co
Level 3, 118 Wendmore Street
Sydney NSW 2000

Font styles to use
Other font styles liked:
• Avenir

Colors
f04a50
ffffff
1b1b1b

Requirements
Must have
• Black back with logo included in the centre of the card.
• Our font is Avenir.

```html
<!DOCTYPE html>
<html lang="en">
<head>
<meta charset="utf-8">
<title>KBT Business Cards</title>
<link rel="stylesheet" href="https://fonts.googleapis.com/css2?family=Nunito+Sans:wght@400;600;700&display=swap">
<style>
  :root {
    --stage: #0c2131;
    --card-black: #262324;
    --card-white: #ffffff;
    --ink: #1b1b1b;
    --brand-red: #b92043;
    --muted: #3a3a3a;
  }
  * { box-sizing: border-box; margin: 0; padding: 0; }
  html, body {
    width: 1200px; height: 907px; overflow: hidden;
    background: var(--stage);
    font-family: "Nunito Sans", "Avenir", sans-serif;
  }
  .canvas {
    position: relative; width: 1200px; height: 907px;
  }
  .card {
    position: absolute;
    width: 520px; height: 318px;
    border-bottom: 6px solid var(--brand-red);
    box-shadow: 0 14px 30px rgba(0,0,0,.45);
  }
  .card--back { left: 50px; top: 150px; background: var(--card-black); }
  .card--front { left: 630px; top: 440px; background: var(--card-white); }

  .firm-mark { display: flex; align-items: flex-start; gap: 12px; }
  .firm-mark__square { width: 22px; height: 22px; background: var(--brand-red); flex: none; margin-top: 3px; }
  .firm-mark__name {
    font-weight: 600; text-transform: uppercase;
    line-height: 1.05; letter-spacing: .02em;
  }
  .card--back .firm-mark {
    position: absolute; left: 50%; top: 50%;
    transform: translate(-50%, -50%);
  }
  .card--back .firm-mark__name { color: var(--card-white); font-size: 26px; }
  .card--front .firm-mark { position: absolute; left: 38px; top: 40px; }
  .card--front .firm-mark__name { color: var(--ink); font-size: 17px; }

  .corner-tab {
    position: absolute; right: 44px; top: 0;
    width: 58px; height: 16px; background: var(--brand-red);
  }
  .person { position: absolute; right: 44px; top: 34px; text-align: right; }
  .person__name { color: var(--brand-red); font-weight: 700; font-size: 22px; }
  .person__role { color: var(--ink); font-size: 14px; margin-top: 2px; }

  .divider {
    position: absolute; left: 38px; right: 44px; top: 200px;
    height: 1.5px; background: var(--brand-red);
  }
  .contacts { position: absolute; left: 38px; top: 218px; list-style: none; }
  .contacts li {
    display: flex; align-items: center; gap: 10px;
    font-size: 14px; color: var(--muted); line-height: 26px;
  }
  .contacts svg { width: 14px; height: 14px; flex: none; }
  .address {
    position: absolute; right: 44px; top: 228px;
    text-align: right; font-style: normal;
    font-size: 13px; color: var(--muted); line-height: 1.45;
  }
</style>
</head>
<body>
<main class="canvas">
  <section class="card card--back" aria-label="Card back">
    <div class="firm-mark">
      <span class="firm-mark__square"></span>
      <span class="firm-mark__name">Kelbrath<br>Bexley Toland<br>Legal</span>
    </div>
  </section>

  <section class="card card--front" aria-label="Card front">
    <div class="firm-mark">
      <span class="firm-mark__square"></span>
      <span class="firm-mark__name">Kelbrath<br>Bexley Toland<br>Legal</span>
    </div>
    <span class="corner-tab"></span>
    <div class="person">
      <p class="person__name">Doran Kelbrath</p>
      <p class="person__role">Partner</p>
    </div>
    <div class="divider"></div>
    <ul class="contacts">
      <li>
        <svg viewBox="0 0 14 14" aria-hidden="true"><circle cx="7" cy="7" r="7" fill="#b92043"/><path d="M4.3 3.6l1.4-.3.7 1.7-.9.7a5 5 0 0 0 2.6 2.6l.7-.9 1.7.7-.3 1.4c-3.4.3-6.2-2.5-5.9-5.9z" fill="#fff"/></svg>
        0461 738 524
      </li>
      <li>
        <svg viewBox="0 0 14 14" aria-hidden="true"><circle cx="7" cy="7" r="7" fill="#b92043"/><rect x="3.5" y="4.5" width="7" height="5" fill="none" stroke="#fff" stroke-width="1"/><path d="M3.5 4.5L7 7.3l3.5-2.8" fill="none" stroke="#fff" stroke-width="1"/></svg>
        doran@kbtlaw.co
      </li>
      <li>
        <svg viewBox="0 0 14 14" aria-hidden="true"><circle cx="7" cy="7" r="7" fill="#b92043"/><circle cx="7" cy="7" r="3.6" fill="none" stroke="#fff" stroke-width="1"/><path d="M3.4 7h7.2M7 3.4c-1.6 2-1.6 5.2 0 7.2M7 3.4c1.6 2 1.6 5.2 0 7.2" fill="none" stroke="#fff" stroke-width=".8"/></svg>
        www.kbtlaw.co
      </li>
    </ul>
    <address class="address">Level 3, 118 Wendmore<br>Street Sydney NSW 2000</address>
  </section>
</main>
</body>
</html>
```